Business card design for Quellmoor Engineering Tandem

We need a new business card design along with all the necessary to place an order. The company is Quellmoor Engineering Tandem and we recently updated our logo.

```html
<!DOCTYPE html>
<html lang="en">
<head>
<meta charset="utf-8">
<title>Quellmoor Engineering Tandem – Business Card</title>
<link rel="stylesheet" href="https://fonts.googleapis.com/css2?family=Montserrat:wght@400;500;600;700&display=swap">
<style>
  :root {
    --page-bg: #3a3a3c;
    --card-bg: #1d1d1e;
    --brand-grey: #a3a3a3;
    --accent-yellow: #e8c22a;
    --text-white: #f2f2f2;
  }
  html, body {
    margin: 0;
    padding: 0;
    width: 1200px;
    height: 1059px;
    overflow: hidden;
    background: var(--page-bg);
    font-family: "Montserrat", sans-serif;
  }
  .canvas {
    position: relative;
    width: 1200px;
    height: 1059px;
  }
  .card {
    position: absolute;
    width: 690px;
    height: 394px;
    border-radius: 22px;
    background: var(--card-bg);
    overflow: hidden;
  }
  .card--front { left: 257px; top: 100px; width: 687px; height: 393px; }
  .card--back  { left: 253px; top: 537px; width: 694px; height: 395px; }

  /* brand */
  .brand {
    display: flex;
    align-items: center;
    gap: 12px;
  }
  .brand__mark {
    flex: none;
    width: 18px;
    height: 18px;
    background: var(--accent-yellow);
  }
  .brand__name {
    margin: 0;
    font-weight: 600;
    font-size: 24px;
    line-height: 30px;
    letter-spacing: 1px;
    text-transform: uppercase;
    color: var(--brand-grey);
    white-space: nowrap;
  }

  /* front */
  .card--front .brand {
    position: absolute;
    left: 28px;
    top: 134px;
    transform: translateY(-50%);
  }
  .person {
    position: absolute;
    right: 24px;
    top: 128px;
    text-align: right;
  }
  .person::after {
    content: "";
    position: absolute;
    right: -24px;
    top: 8px;
    width: 13px;
    height: 54px;
    background: var(--accent-yellow);
  }
  .card--front .person { top: 28px; }
  .person__name {
    margin: 0;
    font-weight: 700;
    font-size: 31px;
    line-height: 36px;
    color: var(--accent-yellow);
    white-space: nowrap;
  }
  .person__title {
    margin: 2px 0 0;
    font-weight: 400;
    font-size: 19px;
    line-height: 24px;
    color: var(--text-white);
  }
  .address {
    position: absolute;
    left: 27px;
    top: 198px;
    margin: 0;
    font-style: normal;
    font-size: 19px;
    line-height: 28px;
    color: var(--text-white);
  }
  .contacts {
    position: absolute;
    left: 27px;
    top: 288px;
    margin: 0;
    padding: 0;
    list-style: none;
  }
  .contacts__item {
    display: flex;
    align-items: center;
    gap: 8px;
    height: 27px;
    font-size: 19px;
    color: var(--text-white);
  }
  .contacts__icon {
    width: 15px;
    height: 15px;
    fill: var(--accent-yellow);
  }
  .front-decoration {
    position: absolute;
    left: 411px;
    top: 147px;
    width: 276px;
    height: 246px;
    background: radial-gradient(ellipse at 60% 20%, #6a6a6a 0%, #333 35%, #131313 70%, var(--card-bg) 100%);
  }

  /* back */
  .back-pattern {
    position: absolute;
    inset: 0;
    background: linear-gradient(120deg, #9e9e9e 0%, #5e5e5e 30%, #262626 55%, #0e0e0e 80%);
  }
  .card--back .brand {
    position: absolute;
    left: 0;
    right: 0;
    top: 197px;
    transform: translateY(-50%);
    justify-content: center;
  }
</style>
</head>
<body>
<main class="canvas">
  <section class="card card--front" aria-label="Business card front">
    <div class="brand">
      <span class="brand__mark"></span>
      <p class="brand__name">Quellmoor<br>Engineering Tandem</p>
    </div>

    <div class="person">
      <p class="person__name">DANIEL REYES</p>
      <p class="person__title">Managing Director</p>
    </div>

    <address class="address">Your address, City<br>State, Zip 1234</address>

    <ul class="contacts">
      <li class="contacts__item">
        <svg class="contacts__icon" viewBox="0 0 16 16" aria-hidden="true"><path d="M1 6c0-2 3-3 7-3s7 1 7 3v1h-4V5.5H5V7H1zM3 8h10l1 6H2z"/></svg>
        123 456 789
      </li>
      <li class="contacts__item">
        <svg class="contacts__icon" viewBox="0 0 16 16" aria-hidden="true"><path d="M1 3h14v1.5L8 9 1 4.5zM1 6l7 4.5L15 6v7H1z"/></svg>
        info@yourgmail.com
      </li>
      <li class="contacts__item">
        <svg class="contacts__icon" viewBox="0 0 16 16" aria-hidden="true"><circle cx="8" cy="8" r="7"/><path d="M5 4c1 1 3 1 3 3s-2 2-2 4M10 11c1-1 3-1 3-3" stroke="#1d1d1e" stroke-width="1.4" fill="none"/></svg>
        www.yourwebsite.com
      </li>
    </ul>

    <div class="front-decoration" role="img" aria-label="Large glossy brand symbol decoration"></div>
  </section>

  <section class="card card--back" aria-label="Business card back">
    <div class="back-pattern" role="img" aria-label="Repeating brand symbol pattern fading from silver to black"></div>
    <div class="brand">
      <span class="brand__mark"></span>
      <p class="brand__name">Quellmoor<br>Engineering Tandem</p>
    </div>
  </section>
</main>
</body>
</html>
```